Animal Eye Clinic needs a Business card

We are a new veterinary ophthalmology practice (Ridgeline Pet Vision Care) and we need a business card designed. We only see animal eyes - we are not a regular veterinary clinic. We already have a logo. We are looking for a professional, good looking business card to hand out to our clients. We are looking for something simple but professional and contemporary. Our logo is likely the only picture/graphic that needs to be on the card.
Updates

Contact Information for Business Card

Delia Vossman, BSc, DVM, MSc, DipACVO
Veterinary Ophthalmologist

Phone: 250.418.3927
Email: ridgelinepetvisioncare@mailbox-example.net
Website: ridgelinepetvisioncare-example.net
Address: 1874 Thornbury Rd
Kelowna, BC, V1X 4M9

Colors

Designer to choose colors to be used in the design.

Requirements
Must have
• Our logo (attached)

```html
<!DOCTYPE html>
<html lang="en">
<head>
<meta charset="utf-8">
<title>Ridgeline Pet Vision Care – Business Card</title>
<link rel="stylesheet" href="https://fonts.googleapis.com/css2?family=Open+Sans:wght@400;600;700&display=swap">
<style>
  :root {
    --backdrop: #3b3532;
    --card: #151515;
    --card-edge: #222222;
    --teal: #1b9aae;
    --text-light: #c4c4c4;
    --text-muted: #9a9a9a;
    --rule: #4a4a4a;
    --silver: #d6d6d6;
  }
  * { margin: 0; padding: 0; box-sizing: border-box; }
  html, body {
    width: 1200px; height: 844px; overflow: hidden;
    background: var(--backdrop);
    font-family: "Open Sans", Arial, sans-serif;
  }
  .stage {
    position: relative; width: 1200px; height: 844px;
    display: flex; align-items: center; justify-content: center; gap: 56px;
  }
  .card {
    position: relative; width: 520px; height: 297px;
    background: var(--card);
    border: 1px solid var(--card-edge);
    box-shadow: 0 10px 30px rgba(0,0,0,.45);
  }
  /* Front */
  .brand {
    position: absolute; top: 52px; left: 150px;
    display: flex; align-items: center; gap: 12px;
  }
  .brand-dot { width: 22px; height: 22px; border-radius: 50%; background: var(--teal); flex: none; }
  .brand-name {
    color: var(--teal); font-weight: 700; font-size: 19px;
    letter-spacing: .5px; text-transform: uppercase; line-height: 1.15;
  }
  .divider {
    position: absolute; top: 118px; left: 150px; right: 40px;
    height: 1px; background: var(--rule);
  }
  .person { position: absolute; left: 34px; top: 160px; }
  .person-name { color: var(--teal); font-weight: 700; font-size: 16px; text-transform: uppercase; }
  .person-credentials { color: var(--text-muted); font-weight: 400; font-size: 11px; text-transform: uppercase; }
  .person-title { color: var(--text-light); font-size: 12.5px; margin-top: 1px; }
  .contact-list { list-style: none; position: absolute; left: 34px; top: 218px; }
  .contact-item {
    display: flex; align-items: center; gap: 8px;
    color: var(--text-light); font-size: 12.5px; line-height: 21px;
  }
  .contact-item svg { width: 12px; height: 12px; flex: none; }
  .address {
    position: absolute; right: 40px; top: 134px; text-align: right;
    color: var(--text-light); font-size: 12.5px; line-height: 19px;
  }
  /* Back */
  .card-back { display: flex; align-items: center; justify-content: center; }
  .back-brand { display: flex; align-items: center; gap: 14px; }
  .back-brand .brand-dot { width: 30px; height: 30px; background: var(--silver); }
  .back-brand .brand-name { color: var(--silver); font-size: 24px; }
</style>
</head>
<body>
<main class="stage">
  <section class="card card-front" aria-label="Business card front">
    <div class="brand">
      <span class="brand-dot"></span>
      <span class="brand-name">Ridgeline Pet<br>Vision Care</span>
    </div>
    <div class="divider"></div>

    <address class="address" style="font-style:normal">
      1874 Thornbury Rd<br>Kelowna, BC, V1X 4M9
    </address>

    <div class="person">
      <div><span class="person-name">Delia Vossman</span><span class="person-credentials">, BSc, DVM, MSc, DipACVO</span></div>
      <div class="person-title">Veterinary Ophthalmologist</div>
    </div>

    <ul class="contact-list">
      <li class="contact-item">
        <svg viewBox="0 0 12 12" aria-hidden="true"><path fill="var(--teal)" d="M2.4 1 4.3 3 3.4 4.3c.6 1.6 1.7 2.7 3.3 3.3L8 6.7l2 1.9-1 1.9C5 10.4 1.6 7 1.5 2.9Z"/></svg>
        250.418.3927
      </li>
      <li class="contact-item">
        <svg viewBox="0 0 12 12" aria-hidden="true"><rect x="1" y="2.5" width="10" height="7" rx="1" fill="var(--teal)"/><path d="M1.5 3 6 6.5 10.5 3" stroke="var(--card)" stroke-width="1" fill="none"/></svg>
        ridgelinepetvisioncare@mailbox-example.net
      </li>
      <li class="contact-item">
        <svg viewBox="0 0 12 12" aria-hidden="true"><circle cx="6" cy="6" r="5" fill="var(--teal)"/><path d="M1 6h10M6 1c-2 2.5-2 7.5 0 10M6 1c2 2.5 2 7.5 0 10" stroke="var(--card)" stroke-width=".8" fill="none"/></svg>
        ridgelinepetvisioncare-example.net
      </li>
    </ul>
  </section>

  <section class="card card-back" aria-label="Business card back">
    <div class="back-brand">
      <span class="brand-dot"></span>
      <span class="brand-name">Ridgeline Pet<br>Vision Care</span>
    </div>
  </section>
</main>
</body>
</html>
```